Business Cards for a law firm

Business cards for our law firm. Use our silhoette logo and OAK PARTNERS - check our website (www.oakpartners.example)

Contact Information for Business Card

our silhouette logo, OAK PARTNERS, 800-555-0147, Dorian Pemberton, dorian@oakpartners.example

Requirements
Must have
• our silhouette logo, OAK PARTNERS, 800-555-0147, Dorian Pemberton, dorian@oakpartners.example

```html
<!DOCTYPE html>
<html lang="en">
<head>
<meta charset="utf-8">
<title>Oak Partners — Business Cards</title>
<link href="https://fonts.googleapis.com/css2?family=Work+Sans:wght@400;500;600;700&display=swap" rel="stylesheet">
<style>
  :root {
    --backdrop: #474c4c;
    --card-white: #efefef;
    --navy: #1f2c5f;
    --navy-deep: #18244f;
    --accent: #e2971f;
    --ink-grey: #555a60;
    --figure-tone: #c6c6d4;
  }
  * { margin: 0; padding: 0; box-sizing: border-box; }
  html, body {
    width: 1200px; height: 1168px; overflow: hidden;
    background: var(--backdrop);
    font-family: "Work Sans", Arial, sans-serif;
  }
  .canvas { position: relative; width: 1200px; height: 1168px; }

  .card {
    position: absolute; left: 245px; width: 702px; height: 401px;
    border-left: 3px solid var(--accent);
    border-bottom: 2px solid var(--accent);
    overflow: hidden;
  }
  .card--front { top: 137px; background: var(--card-white); }
  .card--back { top: 611px; background: var(--navy); }

  .brand {
    position: absolute; left: 30px; top: 36px;
    display: flex; align-items: center; gap: 14px;
  }
  .brand__mark { width: 44px; height: 44px; background: var(--navy); }
  .brand__name {
    font-size: 36px; font-weight: 700; color: var(--navy);
    letter-spacing: 1.2px; line-height: 1;
  }

  .figure-area {
    position: absolute; left: 415px; top: 4px; width: 260px; height: 393px;
    background: linear-gradient(180deg, var(--figure-tone) 0%, #d3d3de 100%);
    border-radius: 40px 40px 6px 6px;
  }

  .details { position: absolute; left: 30px; top: 192px; }
  .details__firm {
    font-size: 24px; font-weight: 700; color: var(--navy);
    letter-spacing: 1.5px; line-height: 1;
  }
  .details__practice {
    margin-top: 10px; font-size: 13px; color: var(--ink-grey);
    letter-spacing: 1.6px; line-height: 1;
  }
  .details__rule {
    width: 22px; height: 2px; background: var(--accent); margin-top: 16px;
  }
  .details__name {
    margin-top: 18px; font-size: 22px; font-weight: 500; color: var(--navy);
    letter-spacing: 1.3px; line-height: 1;
  }
  .details__role {
    margin-top: 7px; font-size: 15px; color: var(--ink-grey);
    letter-spacing: 2.2px; line-height: 1;
  }
  .contact { margin-top: 18px; list-style: none; }
  .contact__item {
    display: flex; align-items: center; gap: 12px;
    font-size: 14px; color: var(--ink-grey); letter-spacing: 1.5px; line-height: 1;
    height: 16px; margin-bottom: 7px; white-space: nowrap;
  }
  .contact__icon { width: 16px; height: 16px; flex: none; }

  .back-brand {
    position: absolute; left: 0; right: 0; top: 172px;
    display: flex; justify-content: center; align-items: center; gap: 16px;
  }
  .back-brand__mark { width: 56px; height: 56px; background: var(--navy-deep); }
  .back-brand__name {
    font-size: 46px; font-weight: 700; color: var(--navy-deep);
    letter-spacing: 1px; line-height: 1;
  }
</style>
</head>
<body>
<main class="canvas">
  <section class="card card--front" aria-label="Business card front">
    <div class="brand">
      <span class="brand__mark"></span>
      <span class="brand__name">OAK PARTNERS</span>
    </div>

    <div class="figure-area" role="img" aria-label="Large faint silhouettes of two standing attorneys in suits"></div>

    <div class="details">
      <p class="details__firm">OAK PARTNERS</p>
      <p class="details__practice">INJURY ATTORNEYS</p>
      <div class="details__rule"></div>
      <p class="details__name">Dorian Pemberton</p>
      <p class="details__role">ATTORNEY</p>
      <ul class="contact">
        <li class="contact__item">
          <svg class="contact__icon" viewBox="0 0 24 24" aria-hidden="true">
            <path d="M6.6 10.8a15.2 15.2 0 0 0 6.6 6.6l2.2-2.2a1 1 0 0 1 1-.25 11.4 11.4 0 0 0 3.6.57 1 1 0 0 1 1 1V20a1 1 0 0 1-1 1A17 17 0 0 1 3 4a1 1 0 0 1 1-1h3.5a1 1 0 0 1 1 1c0 1.25.2 2.450.57 3.57a1 1 0 0 1-.25 1z" fill="#e2971f"/>
            <path d="M14 3a7 7 0 0 1 7 7M14 6.5a3.5 3.5 0 0 1 3.5 3.5" stroke="#e2971f" stroke-width="1.8" fill="none" stroke-linecap="round"/>
          </svg>
          <span>800-555-0147</span>
        </li>
        <li class="contact__item">
          <svg class="contact__icon" viewBox="0 0 24 24" aria-hidden="true">
            <rect x="1" y="4" width="22" height="16" fill="#e2971f"/>
            <path d="M1.5 5 12 13 22.5 5" stroke="#efefef" stroke-width="1.8" fill="none"/>
          </svg>
          <span>dorian@oakpartners.example</span>
        </li>
      </ul>
    </div>
  </section>

  <section class="card card--back" aria-label="Business card back">
    <div class="back-brand">
      <span class="back-brand__mark"></span>
      <span class="back-brand__name">OAK PARTNERS</span>
    </div>
  </section>
</main>
</body>
</html>
```